Valdo Capital

We need a corporate style website design for a new company based in Shenzhen's Qianhai Special Economic Development Zone, China. We provide a range of financial services to large international investment companies. Typically these companies invest over 5 million RMB. The company is part of a group that consists of NorthKilns, ValdoTrusts and ValdoEquity. Our location and gateway into Qianhai Special Economic Zone is our core advantage. We would like to see designs that Do Not use purple and orange. The website design should be similar to other websites in this family but different enough to give it a unique style (See attached website links for reference). The final design should communicate financial safety and growth. This website will act partly as a business chamber with connections to the government so we would like it to be diplomatic in style.

www.northkilns.example
www.valdotrusts.example

*Nevegation Bar
Should including Homepage, Financial Product, Team, News.
Could refer to www.valdotrusts.example

*Contact Details

Miss Lan
Address:E 728, North Block, KMO Centre, East Sector, Shenzhen Bright Science Campus
Telephone: +86 0755 63920417
Cellphone: +86 13957280316

* Social Media
Should be grouped like:
1. Weibo QRcode+ Weibo
2. Facebook, Twitter, Linkedin.

Industry/Entity Type

Investment

```html
<!DOCTYPE html>
<html lang="en">
<head>
<meta charset="utf-8">
<title>Valdo Capital</title>
<link rel="stylesheet" href="https://fonts.googleapis.com/css2?family=Open+Sans:wght@300;400;600;700&display=swap">
<style>
:root{
  --blue:#00aeef;
  --ink:#333333;
  --muted:#555555;
  --dark:#3a3a3a;
  --darker:#2b2b2b;
  --footer:#333333;
  --grey-bg:#ededed;
  --white:#ffffff;
  --line:#dddddd;
}
*{margin:0;padding:0;box-sizing:border-box}
html,body{width:1200px;height:2190px;overflow:hidden}
body{font-family:'Open Sans',Arial,sans-serif;color:var(--ink);background:var(--white);position:relative}
.abs{position:absolute}

/* top bar */
.topbar{left:0;top:0;width:1200px;height:29px;background:var(--dark);color:#eee;font-size:12px}
.topbar .lang{left:115px;top:7px;display:flex;align-items:center;gap:6px}
.topbar .social{right:110px;top:8px;display:flex;gap:8px}
.topbar .social a{width:12px;height:12px;border-radius:50%;background:#ddd;display:block}

/* header */
.header{left:0;top:29px;width:1200px;height:121px;background:var(--white);border-bottom:2px solid var(--blue)}
.brand{left:112px;top:38px;display:flex;align-items:center;gap:14px}
.brand .mark{width:34px;height:34px;background:var(--blue)}
.brand .name{font-size:32px;font-weight:600;color:var(--darker);letter-spacing:.5px}
.nav{left:615px;top:0;height:119px;display:flex}
.nav a{display:flex;align-items:center;justify-content:center;padding-top:18px;font-size:14px;color:var(--ink);text-decoration:none;height:119px}
.nav a.active{background:var(--blue);color:var(--white);font-weight:600}
.nav .w-home{width:74px}
.nav .w-about{width:120px}
.nav .w-partners{width:79px}
.nav .w-news{width:112px}
.nav .w-blog{width:106px}

/* hero */
.hero{left:0;top:150px;width:1200px;height:550px;background:linear-gradient(180deg,#4a5560 0%,#2f3a45 45%,#1f2530 100%);border-bottom:2px solid var(--blue)}
.hero h1{left:0;top:140px;width:1200px;text-align:center;font-size:49px;font-weight:300;color:var(--white)}
.hero h1 b{font-weight:700}
.hero p{left:240px;top:218px;width:720px;text-align:center;font-size:14px;line-height:20px;color:#eee}
.btn{display:inline-block;background:var(--blue);color:var(--white);font-size:14px;font-weight:600;text-align:center;border-radius:2px}
.hero .btn{left:548px;top:302px;width:112px;height:41px;line-height:41px}

/* services */
.services{left:110px;top:610px;width:980px;height:342px;background:var(--white);box-shadow:0 2px 6px rgba(0,0,0,.12)}
.services h2{left:0;top:18px;width:980px;text-align:center;font-size:20px;font-weight:400}
.service{top:60px;width:210px;text-align:center}
.service .photo{width:210px;height:133px;border:1px solid var(--line)}
.service h3{margin-top:15px;font-size:16px;font-weight:400;color:var(--ink)}
.service h3.current{color:var(--blue)}
.service p{margin:6px auto 0;width:202px;font-size:11.5px;line-height:16px;color:var(--muted)}
.service .btn{margin-top:12px;width:85px;height:30px;line-height:30px;font-size:12.5px;font-weight:400}
.arrow{top:108px;width:34px;height:32px;background:var(--blue);display:flex;align-items:center;justify-content:center}

/* key section */
.key h2{left:118px;top:1037px;font-size:20px;font-weight:400}
.key p{left:118px;top:1069px;width:590px;font-size:12.5px;line-height:20px;color:var(--muted)}
.how-photo{left:149px;top:1169px;width:256px;height:256px;border-radius:50%;background:linear-gradient(160deg,#dfe7ee,#a9bccb 60%,#5d86b0)}
.how h2{left:537px;top:1147px;font-size:21px;font-weight:400}
.how p.lead{left:537px;top:1182px;width:555px;font-size:12.5px;line-height:20px;color:var(--muted)}
.checks{left:537px;top:1235px;list-style:none}
.checks li{display:flex;align-items:center;gap:12px;height:44px;font-size:12.5px;color:var(--muted)}

/* blog + about */
.band{left:0;top:1467px;width:1200px;height:409px;background:var(--grey-bg)}
.blog h2,.about h2{font-size:18px;font-weight:400}
.blog h2{left:112px;top:1486px}
.blog-head{left:112px;top:1520px;width:592px;height:35px;background:var(--dark);color:var(--white);font-size:13px;display:flex;align-items:center;padding-left:8px}
.blog-head .tools{position:absolute;right:0;top:0;display:flex}
.blog-head .tools span{width:38px;height:35px;background:var(--blue);border-left:1px solid #0a8fc4;display:flex;align-items:center;justify-content:center}
.posts{left:112px;top:1558px;width:592px;list-style:none}
.posts li{height:52px;margin-bottom:3px;background:var(--white);display:flex;align-items:center;justify-content:space-between;padding:0 24px 0 6px;font-size:13.5px;color:var(--ink)}
.posts li.current{color:var(--blue)}
.view-all{left:664px;top:1832px;font-size:11px;font-style:italic;color:var(--blue)}
.about h2{left:739px;top:1486px}
.about p{left:739px;top:1523px;width:345px;font-size:12.5px;line-height:20px;color:var(--ink)}
.about .btn{left:739px;top:1774px;width:98px;height:31px;line-height:31px;background:#777;font-weight:400;font-size:13px}

/* footer */
.footer{left:0;top:1876px;width:1200px;height:256px;background:var(--footer);color:#eee}
.footer .brand-f{left:100px;top:100px;width:250px;display:flex;align-items:center;justify-content:center;gap:10px;font-size:24px;font-weight:600;color:var(--white)}
.footer .brand-f .mark{width:24px;height:24px;background:var(--blue)}
.footer .icons{left:123px;top:184px;display:flex;gap:8px}
.footer .icons a{width:28px;height:28px;border-radius:50%;background:var(--white);display:block}
.col h3{font-size:15px;font-weight:600;color:var(--white)}
.sitemap{left:419px;top:46px}
.sitemap ul{list-style:none;margin-top:12px;font-size:12.5px;line-height:16px}
.contact{left:606px;top:46px;width:190px}
.contact .row{display:flex;gap:10px;margin-top:8px;font-size:12.5px;line-height:16px}
.contact .row svg{flex:none;margin-top:2px}
.findus{left:831px;top:46px}
.map{left:831px;top:74px;width:257px;height:165px;background:linear-gradient(135deg,#f1efe6,#e3e0d0);border:1px solid #ccc}
.divider{top:48px;width:1px;height:160px;background:#4c4c4c}
.copyright{left:0;top:2132px;width:1200px;height:58px;background:var(--darker);color:#ccc;font-size:12.5px;text-align:center;line-height:58px}
</style>
</head>
<body>

<div class="topbar abs">
  <div class="lang abs">
    <svg width="14" height="14" viewBox="0 0 14 14"><circle cx="7" cy="7" r="6" fill="none" stroke="#eee" stroke-width="1.4"/><path d="M1 7h12M7 1c3 3 3 9 0 12M7 1c-3 3-3 9 0 12" stroke="#eee" fill="none"/></svg>
    <span>English(UK) ▾</span><span>&nbsp;|&nbsp;</span>
    <svg width="9" height="12" viewBox="0 0 9 12"><path d="M2 1l2 2-1 2 2 3 2-1 1 2-2 2C3 10 1 5 2 1z" fill="#eee"/></svg>
    <span>Contact Us : +123 234 456 678</span>
  </div>
  <div class="social abs">
    <a href="#" aria-label="Social network page"></a><a href="#" aria-label="Social network page"></a><a href="#" aria-label="Messaging contact"></a><a href="#" aria-label="Microblog page"></a><a href="#" aria-label="News feed"></a><a href="#" aria-label="Professional network page"></a><a href="#" aria-label="Video channel"></a>
  </div>
</div>

<header class="header abs">
  <div class="brand abs"><span class="mark"></span><span class="name">Valdo Capital</span></div>
  <nav class="nav abs">
    <a class="active w-home" href="#">HOME</a>
    <a class="w-about" href="#">About Us</a>
    <a class="w-partners" href="#">Partners</a>
    <a class="w-news" href="#">News/Info</a>
    <a class="w-blog" href="#">Valdo Blog</a>
  </nav>
</header>

<section class="hero abs" role="img" aria-label="Night skyline of a financial district">
  <h1 class="abs">Welcome to <b>Valdo Capital</b></h1>
  <p class="abs">Lorem Ipsum is simply dummy text of the printing and typesetting industry. Lorem Ipsum has been the industry's standard dummy text ever since the 1500s, when an unknown printer took a galley of type and scrambled it to make a type specimen book.</p>
  <a class="btn abs">Read More</a>
</section>

<section class="services abs">
  <h2 class="abs">Our Services</h2>
  <div class="service abs" style="left:26px">
    <div class="photo" role="img" aria-label="Business people meeting" style="background:linear-gradient(160deg,#c9d3dc,#3d4a5a)"></div>
    <h3 class="current">Consultancy</h3>
    <p>Lorem Ipsum is simply dummy text of the printing and typesetting industry.</p>
    <a class="btn">Read More</a>
  </div>
  <div class="service abs" style="left:265px">
    <div class="photo" role="img" aria-label="Hands sheltering a coin stack" style="background:linear-gradient(180deg,#f6f4ef,#e4d6bf)"></div>
    <h3>Finance</h3>
    <p>Lorem Ipsum is simply dummy text of the printing and typesetting industry.</p>
    <a class="btn">Read More</a>
  </div>
  <div class="service abs" style="left:503px">
    <div class="photo" role="img" aria-label="House model on building plans" style="background:linear-gradient(160deg,#e9ecee,#a9aeb2)"></div>
    <h3>Property Management</h3>
    <p>Lorem Ipsum is simply dummy text of the printing and typesetting industry.</p>
    <a class="btn">Read More</a>
  </div>
  <div class="service abs" style="left:743px">
    <div class="photo" role="img" aria-label="Hand holding house keys" style="background:linear-gradient(160deg,#f0f0f0,#c9b9a8)"></div>
    <h3>Theme Real Estate</h3>
    <p>Lorem Ipsum is simply dummy text of the printing and typesetting industry.</p>
    <a class="btn">Read More</a>
  </div>
  <div class="arrow abs" style="left:18px"><svg width="8" height="10"><path d="M7 0v10L0 5z" fill="#fff"/></svg></div>
  <div class="arrow abs" style="left:927px"><svg width="8" height="10"><path d="M1 0v10l7-5z" fill="#fff"/></svg></div>
</section>

<section class="key">
  <h2 class="abs">Valdo Capital is the Key to Success</h2>
  <p class="abs">Lorem ipsum dolor sit amet, consectetur adipisicing elit, sed do eiusmod tempor incididunt ut labore et dolore magna aliqua. Ut enim ad minim veniam, quis nostrud exercitation ullamco laboris nisi ut aliquip ex ea commodo consequat.</p>
</section>

<section class="how">
  <div class="how-photo abs" role="img" aria-label="Team reviewing financial charts"></div>
  <svg class="abs" style="left:370px;top:1160px" width="105" height="60" viewBox="0 0 105 60"><path d="M2 58C20 25 55 8 95 6" stroke="#1aa3e0" stroke-width="3" fill="none"/><path d="M86 0l17 6-16 7z" fill="#1aa3e0"/></svg>
  <h2 class="abs">Need to Know How We Work</h2>
  <p class="lead abs">Lorem ipsum dolor sit amet, consectetur adipisicing elit, sed do eiusmod tempor incididunt ut labore et dolore magna aliqua. Ut enim ad minim veniam, quis nostrud exercitation.</p>
  <ul class="checks abs">
    <li><svg width="17" height="17"><circle cx="8.5" cy="8.5" r="8.5" fill="#00aeef"/><path d="M4.5 9l3 3 5-6" stroke="#fff" stroke-width="2" fill="none"/></svg>Sed ut perspiciatis unde omnis iste natus error sit.</li>
    <li><svg width="17" height="17"><circle cx="8.5" cy="8.5" r="8.5" fill="#00aeef"/><path d="M4.5 9l3 3 5-6" stroke="#fff" stroke-width="2" fill="none"/></svg>Sed ut perspiciatis unde omnis iste natus error sit voluptatem</li>
    <li><svg width="17" height="17"><circle cx="8.5" cy="8.5" r="8.5" fill="#00aeef"/><path d="M4.5 9l3 3 5-6" stroke="#fff" stroke-width="2" fill="none"/></svg>Lorem ipsum dolor sit amet, consectetur adipisicing elit.</li>
    <li><svg width="17" height="17"><circle cx="8.5" cy="8.5" r="8.5" fill="#00aeef"/><path d="M4.5 9l3 3 5-6" stroke="#fff" stroke-width="2" fill="none"/></svg>Ut enim ad minim veniam, quis nostrud exercitation ullamco.</li>
  </ul>
</section>

<div class="band abs"></div>
<section class="blog">
  <h2 class="abs">Valdo Blog</h2>
  <div class="blog-head abs">Recent Posts from the blog
    <div class="tools">
      <span><svg width="14" height="14"><circle cx="6" cy="6" r="4.5" stroke="#fff" stroke-width="2" fill="none"/><path d="M9 9l4 4" stroke="#fff" stroke-width="2"/></svg></span>
      <span><svg width="14" height="14"><path d="M1 1h6l6 6-6 6-6-6z" fill="#fff"/><circle cx="4" cy="4" r="1.3" fill="#00aeef"/></svg></span>
      <span><svg width="18" height="14"><circle cx="6" cy="4" r="3" fill="#fff"/><path d="M0 14c0-5 12-5 12 0z" fill="#fff"/><circle cx="13" cy="4" r="2.5" fill="#fff"/><path d="M12 9c3-1 6 1 6 5h-5z" fill="#fff"/></svg></span>
    </div>
  </div>
  <ul class="posts abs">
    <li class="current">Lorem ipsum dolor sit amet, consectetur adipisicing elit, sed do eiusmod tempor<svg width="13" height="13"><circle cx="6.5" cy="6.5" r="6.5" fill="#00aeef"/><path d="M3.5 5l3 3 3-3" stroke="#fff" stroke-width="1.6" fill="none"/></svg></li>
    <li>Lorem ipsum dolor sit amet, consectetur adipisicing elit,<svg width="13" height="13"><circle cx="6.5" cy="6.5" r="6.5" fill="#999"/><path d="M3.5 5l3 3 3-3" stroke="#fff" stroke-width="1.6" fill="none"/></svg></li>
    <li>Lorem ipsum dolor sit amet, consectetur adipisicing elit, Sed do eiusmod tempor<svg width="13" height="13"><circle cx="6.5" cy="6.5" r="6.5" fill="#999"/><path d="M3.5 5l3 3 3-3" stroke="#fff" stroke-width="1.6" fill="none"/></svg></li>
    <li>Lorem ipsum dolor sit amet, consectetur adipisicing elit, Sed do eiusmod tempor<svg width="13" height="13"><circle cx="6.5" cy="6.5" r="6.5" fill="#999"/><path d="M3.5 5l3 3 3-3" stroke="#fff" stroke-width="1.6" fill="none"/></svg></li>
    <li>Lorem ipsum dolor sit amet, consectetur adipisicing elit<svg width="13" height="13"><circle cx="6.5" cy="6.5" r="6.5" fill="#999"/><path d="M3.5 5l3 3 3-3" stroke="#fff" stroke-width="1.6" fill="none"/></svg></li>
  </ul>
  <a class="view-all abs">View All</a>
</section>
<section class="about">
  <h2 class="abs">About Us</h2>
  <p class="abs">Lorem Ipsum is simply dummy text of the printing and typesetting industry. Lorem Ipsum has been the industry's standard dummy text ever since the 1500s, when an unknown printer took a galley of type and scrambled it to make a type specimen book. It has survived not only five centuries, but also the leap into electronic typesetting, remaining essentially unchanged. It was popularised in the 1960s with the release of Quillset sheets containing Lorem Ipsum passages, and more recently with desktop publishing software like Orvel PageSmith including versions of Lorem Ipsum.</p>
  <a class="btn abs">Read More</a>
</section>

<footer class="footer abs">
  <div class="brand-f abs"><span class="mark"></span><span>Valdo Capital</span></div>
  <div class="icons abs">
    <a href="#" aria-label="Microblog page"></a>
    <a href="#" aria-label="Microblog feed"></a>
    <a href="#" aria-label="Professional network page"></a>
    <a href="#" aria-label="Social network page"></a>
    <a href="#" aria-label="Community page"></a>
  </div>
  <div class="divider abs" style="left:555px"></div>
  <div class="divider abs" style="left:799px"></div>
  <div class="col sitemap abs">
    <h3>Site Map</h3>
    <ul><li>Home</li><li>About Us</li><li>Investment Fields</li><li>Partners</li><li>News/Info</li><li>Valdo Blog</li></ul>
  </div>
  <div class="col contact abs">
    <h3>Contact Us</h3>
    <div class="row"><svg width="14" height="12"><path d="M7 0l7 6h-2v6H9V8H5v4H2V6H0z" fill="#eee"/></svg><span>E 728, North Block, KMO Centre, East Sector, Shenzhen Bright Science Campus</span></div>
    <div class="row"><svg width="14" height="12"><path d="M3 0l2 2-1 2 3 4 2-1 2 2-2 3C4 11 1 5 3 0z" fill="#eee"/></svg><span>+86 0755 63920417</span></div>
    <div class="row"><svg width="14" height="12"><rect x="3" y="0" width="8" height="12" rx="1" fill="#eee"/><rect x="4.5" y="2" width="5" height="6" fill="#333"/></svg><span>+86 13957280316</span></div>
  </div>
  <div class="col findus abs"><h3>Find Us</h3></div>
  <div class="map abs" role="img" aria-label="Street map of the office location"></div>
</footer>
<div class="copyright abs">Copyright © 2014 Valdo Capital . All rights reserved.</div>

</body>
</html>
```